Small Business Broker Business Card Design

A business card design for a small business brokerage, which is a financial service, not unlike real estate brokerage, but for small businesses such as laundromats, pizza shops, restaurants, cleaners etc. The designs should all be simple, more conservative in nature, using the colors and font of the logo. Again, think real estate Brokerage as a business context
Contact Information for Business Card
Name: Glen R. Harlow. Title: Small Business Advisor. Email: g.harlow@bayfieldcapitalworks.example. Mobile: (555) 274-3918. Office: (555) 806-2147. www.bayfieldcapitalworks.example

```html
<!DOCTYPE html>
<html lang="en">
<head>
<meta charset="utf-8">
<title>Bayfield Capital Works – Business Card</title>
<link href="https://fonts.googleapis.com/css2?family=Open+Sans:wght@400;600;700;800&display=swap" rel="stylesheet">
<style>
  :root {
    --navy: #1b3a6b;
    --green: #8cc63f;
    --ink: #1a1a1a;
    --paper: #ffffff;
    --backdrop: #dcdcdc;
  }
  * { box-sizing: border-box; margin: 0; padding: 0; }
  html, body {
    width: 1200px; height: 780px; overflow: hidden;
    background: var(--backdrop);
    font-family: "Open Sans", Arial, sans-serif;
  }
  .stage {
    width: 1200px; height: 780px;
    display: flex; align-items: center; justify-content: center; gap: 40px;
  }
  .card {
    position: relative;
    width: 540px; height: 309px;
    background: var(--paper);
    border-radius: 22px;
    overflow: hidden;
  }
  .card__shapes { position: absolute; inset: 0; width: 100%; height: 100%; }
  .card__shapes .accent-green { fill: var(--green); }
  .card__shapes .accent-navy { fill: var(--navy); }

  .brand {
    position: absolute;
    display: flex; align-items: center; gap: 10px;
    color: var(--navy);
    font-weight: 800;
    text-transform: uppercase;
    letter-spacing: 0.04em;
    white-space: nowrap;
  }
  .brand__mark { width: 14px; height: 14px; background: var(--navy); flex: none; }

  .card--front .brand { left: 50%; top: 50%; transform: translate(-50%, -50%); font-size: 22px; }

  .card--back .brand {
    left: 56px; top: 138px; width: 190px;
    font-size: 13px; line-height: 1.25; gap: 8px;
    white-space: normal;
  }
  .card--back .brand__mark { width: 11px; height: 11px; }

  .divider {
    position: absolute; left: 262px; top: 42px;
    width: 1px; height: 176px; background: var(--ink);
  }
  .contact { position: absolute; left: 280px; top: 46px; color: var(--ink); }
  .contact__name { font-size: 25px; font-weight: 800; line-height: 1.1; }
  .contact__name .first { color: var(--green); }
  .contact__name .last { color: var(--navy); }
  .contact__title { font-size: 14px; font-weight: 600; margin: 4px 0 12px; }
  .contact__list { list-style: none; font-size: 11px; line-height: 1.85; }
  .contact__list li { display: flex; align-items: center; gap: 8px; }
  .contact__list svg { width: 12px; height: 12px; fill: var(--green); flex: none; }

  .address {
    position: absolute; left: 0; right: 0; bottom: 34px;
    text-align: center; font-size: 14px; color: var(--ink);
  }
</style>
</head>
<body>
<main class="stage">

  <section class="card card--front" aria-label="Card front">
    <svg class="card__shapes" viewBox="0 0 540 309" preserveAspectRatio="none" aria-hidden="true">
      <path class="accent-green" d="M0,0 H165 Q45,75 34,309 H0 Z"/>
      <path class="accent-navy" d="M540,115 Q522,262 345,309 H540 Z"/>
    </svg>
    <div class="brand"><span class="brand__mark"></span>Bayfield Capital Works, Inc</div>
  </section>

  <section class="card card--back" aria-label="Card back">
    <svg class="card__shapes" viewBox="0 0 540 309" preserveAspectRatio="none" aria-hidden="true">
      <path class="accent-green" d="M0,0 H150 Q45,70 34,230 V309 H0 Z"/>
      <path class="accent-navy" d="M540,100 Q520,255 350,309 H540 Z"/>
    </svg>

    <div class="brand"><span class="brand__mark"></span>Bayfield Capital Works, Inc</div>

    <div class="divider"></div>

    <div class="contact">
      <h1 class="contact__name"><span class="first">Glen</span> <span class="last">R. Harlow</span></h1>
      <p class="contact__title">Small Business Advisor</p>
      <ul class="contact__list">
        <li><svg viewBox="0 0 24 24"><path d="M6.6 10.8a15.1 15.1 0 0 0 6.6 6.6l2.2-2.2a1 1 0 0 1 1-.25 11.4 11.4 0 0 0 3.6.57 1 1 0 0 1 1 1V20a1 1 0 0 1-1 1A17 17 0 0 1 3 4a1 1 0 0 1 1-1h3.5a1 1 0 0 1 1 1c0 1.25.2 2.45.57 3.57a1 1 0 0 1-.25 1z"/></svg>(555) 274-3918</li>
        <li><svg viewBox="0 0 24 24"><path d="M2 5h20v14H2z M4 7v.5l8 5 8-5V7l-8 5z" fill-rule="evenodd"/></svg>g.harlow@bayfieldcapitalworks.example</li>
        <li><svg viewBox="0 0 24 24"><circle cx="12" cy="12" r="10"/></svg>www.bayfieldcapitalworks.example</li>
      </ul>
    </div>

    <p class="address">1480 Larkspur Ave. Suite 300 Millbrook, TX 75001</p>
  </section>

</main>
</body>
</html>
```